Coastline Premier Retreats Business Card Design

Design a business card for Coastline Premier Retreats. Look at the website for colors and reference. Card should have logo, name, title, office number, mobile number, email, URL and a tagline like, "Luxury Hotel & Resort Email Marketing" (This might change).

https://www.coastlinepremierretreats.example

The rest I will leave up to your imagination.

Contact Information for Business Card

Logo, name, title, office number, mobile number, email, URL and a tagline like, "Luxury Hotel & Resort Email Marketing" (This might change).

```html
<!DOCTYPE html>
<html lang="en">
<head>
<meta charset="utf-8">
<title>Coastline Premier Retreats – Business Card</title>
<link rel="stylesheet" href="https://fonts.googleapis.com/css2?family=Michroma&family=Open+Sans:wght@400;600&display=swap">
<style>
  :root {
    --backdrop: #2f2f2f;
    --card: #141414;
    --card-edge: #1c1c1c;
    --accent: #f07a1e;
    --ink-light: #f2f2f2;
    --ink-muted: #d8d8d8;
    --ink-dark: #111111;
  }
  * { box-sizing: border-box; margin: 0; padding: 0; }
  html, body { width: 1200px; height: 801px; overflow: hidden; }
  body {
    background: var(--backdrop);
    display: flex;
    align-items: center;
    justify-content: center;
    gap: 40px;
  }
  .card {
    position: relative;
    width: 540px;
    height: 309px;
    background: var(--card);
    border: 1px solid var(--card-edge);
    overflow: hidden;
    box-shadow: 0 14px 30px rgba(0,0,0,.45);
  }

  /* Front */
  .brand-name {
    position: absolute;
    top: 46px;
    left: 0;
    right: 0;
    text-align: center;
    font-family: "Michroma", sans-serif;
    font-weight: 400;
    color: var(--ink-light);
    line-height: 1.1;
  }
  .brand-name .brand-main { display: block; font-size: 32px; letter-spacing: 1px; }
  .brand-name .brand-sub { display: block; font-size: 13px; letter-spacing: 5px; margin-top: 6px; }

  .details {
    position: absolute;
    top: 150px;
    left: 40px;
    right: 30px;
    display: flex;
    align-items: center;
  }
  .person { width: 200px; text-align: right; padding-right: 22px; }
  .person-name {
    font-family: "Michroma", sans-serif;
    font-size: 16px;
    color: var(--accent);
    letter-spacing: .5px;
  }
  .person-title {
    font-family: "Open Sans", sans-serif;
    font-size: 14px;
    color: var(--ink-muted);
    margin-top: 4px;
  }
  .divider { width: 1px; height: 70px; background: var(--accent); }
  .contacts { list-style: none; padding-left: 22px; }
  .contacts li {
    display: flex;
    align-items: center;
    gap: 8px;
    font-family: "Open Sans", sans-serif;
    font-size: 13px;
    color: var(--ink-light);
    line-height: 1.75;
  }
  .contacts svg { width: 12px; height: 12px; flex: none; }

  .tagline-band {
    position: absolute;
    left: 0; right: 0; bottom: 18px;
    height: 36px;
    background: var(--accent);
    display: flex;
    align-items: center;
    justify-content: center;
    font-family: "Michroma", sans-serif;
    font-size: 13px;
    letter-spacing: 3px;
    color: var(--ink-dark);
  }

  /* Back */
  .pattern-field {
    position: absolute;
    inset: 0;
    background: linear-gradient(120deg, #101010 0%, #1d1d1d 45%, #262626 70%, #151515 100%);
  }
  .back-brand {
    position: absolute;
    right: 70px;
    bottom: 70px;
    display: flex;
    align-items: center;
    gap: 8px;
    font-family: "Michroma", sans-serif;
    font-size: 12px;
    letter-spacing: 1px;
    color: var(--ink-light);
  }
  .back-brand .mark { width: 10px; height: 10px; background: var(--accent); }
</style>
</head>
<body>
  <section class="card card-front">
    <div class="brand-name">
      <span class="brand-main">COASTLINE</span>
      <span class="brand-sub">PREMIER RETREATS</span>
    </div>

    <div class="details">
      <div class="person">
        <p class="person-name">DANA WHITFORD</p>
        <p class="person-title">President / CEO</p>
      </div>
      <div class="divider"></div>
      <ul class="contacts">
        <li>
          <svg viewBox="0 0 24 24" aria-hidden="true"><path fill="var(--accent)" d="M6.6 10.8a15.1 15.1 0 0 0 6.6 6.6l2.2-2.2c.3-.3.7-.4 1-.2 1.1.4 2.3.6 3.6.6.6 0 1 .4 1 1V20c0 .6-.4 1-1 1A17 17 0 0 1 3 4c0-.6.4-1 1-1h3.5c.6 0 1 .4 1 1 0 1.3.2 2.5.6 3.6.1.3 0 .7-.2 1z"/></svg>
          555.010.4820
        </li>
        <li>
          <svg viewBox="0 0 24 24" aria-hidden="true"><path fill="var(--accent)" d="M2 5h20v14H2z"/><path fill="none" stroke="var(--card)" stroke-width="2" d="M3 6l9 7 9-7"/></svg>
          info@coastlinepremierretreats.example
        </li>
        <li>
          <svg viewBox="0 0 24 24" aria-hidden="true"><circle cx="12" cy="12" r="10" fill="var(--accent)"/><path fill="none" stroke="var(--card)" stroke-width="1.6" d="M2 12h20M12 2c3 3 3 17 0 20M12 2c-3 3-3 17 0 20"/></svg>
          www.coastlinepremierretreats.example
        </li>
      </ul>
    </div>

    <div class="tagline-band">LUXURY HOTEL &amp; RESORT EMAIL MARKETING</div>
  </section>

  <section class="card card-back">
    <div class="pattern-field" role="img" aria-label="Subtle embossed repeating brand pattern in dark grey tones"></div>
    <div class="back-brand"><span class="mark"></span>COASTLINE PREMIER RETREATS</div>
  </section>
</body>
</html>
```